Business card design needed

I would like a one sided black business card with the information provided above. Refer to my website www.brightvolleyracquets.com.au for an example of colors I have used for my site, would like to keep this consistent for my business cards also, I will upload my logo below.

I am a new small business that provides tennis customers with racquet re stringing, tennis strings and accessories.

Industry/Entity Type

Small Business

Contact Information for Business Card

Bright Volley Tennis

Owen Whitby
Managing Director

brightvolleyracquets@mailbox.example
www.brightvolleyracquets.com.au
0491 726 305

Racquet Restringing/Tennis Strings/Accessories

Requirements
Must have
• Must have my logo and card must be black

```html
<!DOCTYPE html>
<html lang="en">
<head>
<meta charset="utf-8">
<title>Bright Volley Tennis – Business Card</title>
<link rel="stylesheet" href="https://fonts.googleapis.com/css2?family=Arimo:wght@400;700&display=swap">
<style>
  :root {
    --backdrop: #e9e6e2;
    --card-black: #000000;
    --lime: #c3dc34;
    --navy: #234a86;
    --white: #ffffff;
    --divider: #9a9a9a;
  }
  * { margin: 0; padding: 0; box-sizing: border-box; }
  html, body { width: 1200px; height: 475px; overflow: hidden; }
  body {
    background: var(--backdrop);
    font-family: "Arimo", Arial, sans-serif;
    position: relative;
  }
  .card {
    position: absolute;
    width: 547px;
    height: 313px;
    background: var(--card-black);
    border-radius: 20px;
    overflow: hidden;
  }
  .card--front { left: 31px; top: 81px; }
  .card--back { left: 607px; top: 86px; }

  .brand {
    position: absolute;
    left: 0; right: 0;
    display: flex;
    align-items: center;
    justify-content: center;
    gap: 10px;
    color: var(--lime);
    font-weight: 700;
    letter-spacing: 1px;
    text-transform: uppercase;
    white-space: nowrap;
  }
  .brand__dot {
    width: 20px; height: 20px;
    border-radius: 50%;
    background: var(--lime);
    flex: none;
  }
  .card--front .brand { top: 62px; font-size: 28px; }
  .card--back .brand { top: 108px; font-size: 30px; }

  .holder {
    position: absolute;
    right: 303px;
    top: 168px;
    text-align: right;
    color: var(--lime);
    white-space: nowrap;
  }
  .holder__name { font-size: 18px; letter-spacing: 0.5px; text-transform: uppercase; }
  .holder__role { font-size: 14px; margin-top: 3px; }

  .divider {
    position: absolute;
    left: 254px; top: 164px;
    width: 1px; height: 66px;
    background: var(--divider);
  }
  .contact {
    position: absolute;
    left: 266px; top: 168px;
    list-style: none;
    color: var(--white);
    font-size: 13px;
    line-height: 19px;
    white-space: nowrap;
  }
  .contact__label { display: inline-block; width: 14px; }

  .swoosh { position: absolute; left: 0; top: 0; }

  .web {
    position: absolute;
    left: 0; right: 0; top: 251px;
    text-align: center;
    color: var(--white);
    font-size: 13.5px;
    letter-spacing: 2.2px;
    white-space: nowrap;
  }
</style>
</head>
<body>
  <section class="card card--front" aria-label="Business card front">
    <svg class="swoosh" width="547" height="313" viewBox="0 0 547 313" aria-hidden="true">
      <path d="M0 222 Q230 300 547 246 L547 313 L0 313 Z" fill="var(--navy)"/>
      <path d="M0 200 Q150 268 440 266 Q230 270 0 214 Z" fill="var(--lime)"/>
    </svg>
    <div class="brand"><span class="brand__dot"></span><span>Bright Volley Tennis</span></div>
    <div class="holder">
      <p class="holder__name">Owen Whitby</p>
      <p class="holder__role">Managing Director</p>
    </div>
    <div class="divider"></div>
    <ul class="contact">
      <li><span class="contact__label">P</span>: 0491 726 305</li>
      <li><span class="contact__label">E</span>: brightvolleyracquets@mailbox.example</li>
      <li><span class="contact__label">W</span>: www.brightvolleyracquets.com.au</li>
    </ul>
  </section>

  <section class="card card--back" aria-label="Business card back">
    <div class="brand"><span class="brand__dot"></span><span>Bright Volley Tennis</span></div>
    <p class="web">www.brightvolleyracquets.com.au</p>
  </section>
</body>
</html>
```